DESKHAVEN COSPACE Website design and coding

DESKHAVEN COSPACE

DESKHAVEN is Galveston’s first (and currently only) shared business co-working space. We share the same upscale, casual work environment, but we work independently on our own (or our team’s) projects and goals. For only a flat $195 membership fee per month, you have your very own all-inclusive, fun, personal business office environment. Website is written (Word file #12, below); and all pictures etc provided. Galveston is a beachy, coastal, historic city an hour from Houston, Texas USA. Logo (file 11 below) is temporary only.

Target Market(s)

Outside sales people, medical students looking for study hall, Houston companies looking for local office, real estate agents, graphic artists, entrepreneurs, etc

Contact Information for Business Card

will discuss --want to combine with current business card with multiple businesses

Logo Text

DESKHAVEN COSPACE

Coding

Coded - Design and coding required

Number of Pages Required

5+ page

Colors
ec1f27
fbed22

Requirements
Nice to have
• maroon/wine dominant with yellow and red accents, gray base are the colors of the space--website could coordinate--but open to creative ideas/combinations

```html
<!DOCTYPE html>
<html lang="en">
<head>
<meta charset="utf-8">
<title>Deskhaven Cospace</title>
<link href="https://fonts.googleapis.com/css2?family=Montserrat:wght@600;700&family=Lato:wght@400;700&display=swap" rel="stylesheet">
<style>
:root{
  --blue:#35a8e0;
  --ink:#1b1b1b;
  --text:#555a60;
  --white:#ffffff;
  --card-dark:#1c1c1e;
  --line:#c9ced3;
}
*{margin:0;padding:0;box-sizing:border-box}
html,body{width:1200px;height:3899px;overflow:hidden;background:var(--white)}
body{position:relative;font-family:'Lato',sans-serif;color:var(--text)}
.abs{position:absolute}
.heading{font-family:'Montserrat',sans-serif;font-weight:700;color:var(--ink);letter-spacing:.5px}
.rule{position:absolute;height:3px;background:var(--blue)}

/* hero */
.hero{left:0;top:0;width:1200px;height:627px;background:linear-gradient(180deg,#3c3f45 0%,#5b5450 35%,#9a7337 65%,#c08c3c 85%,#8a6a3a 100%);border-top:3px solid var(--blue)}
.hero-shade{left:0;top:0;width:1200px;height:627px;background:linear-gradient(180deg,rgba(0,0,0,.25),rgba(0,0,0,.05) 60%,rgba(0,0,0,.15))}
.brand{left:109px;top:26px;font-family:'Montserrat',sans-serif;font-weight:700;font-size:25px;line-height:34px;color:var(--white)}
.nav{left:360px;top:54px;display:flex;gap:25px;font-size:13px;color:var(--white);letter-spacing:.2px}
.nav span{padding-bottom:8px}
.nav .active{color:var(--blue);border-bottom:3px solid var(--blue)}
.hero-title{left:0;width:1200px;top:240px;text-align:center;font-family:'Montserrat',sans-serif;font-weight:700;font-size:54px;color:var(--white);letter-spacing:1px}
.hero-sub{left:0;width:1200px;top:310px;text-align:center;font-size:15.5px;line-height:26px;color:var(--white)}
.btn-start{left:527px;top:378px;width:148px;height:49px;background:var(--blue);color:var(--white);font-weight:700;font-size:14px;display:flex;align-items:center;justify-content:center;border-radius:2px}
.dots{left:568px;top:549px;display:flex;gap:5px}
.dots i{width:12px;height:12px;border:2px solid var(--white);border-radius:50%}
.dots i.on{border-color:var(--blue)}

/* about */
.about-title{left:0;width:1200px;top:710px;text-align:center;font-size:41px}
.about-text{left:195px;width:810px;top:790px;text-align:center;font-size:14px;line-height:26px}

/* amenities */
.amen-photo{left:0;top:955px;width:600px;height:494px;background:linear-gradient(120deg,#6b2a33 0%,#8a3a40 20%,#d9d6cf 45%,#b9b4aa 60%,#2a2a2a 80%,#4a3a36 100%)}
.amen-panel{left:600px;top:955px;width:600px;height:494px;background:var(--blue)}
.amen-title{left:660px;top:1030px;font-size:40px;color:var(--white)}
.amen-list{left:660px;top:1106px;width:480px;list-style:none;color:var(--white);font-size:13px;line-height:17px}
.amen-list li{display:flex;gap:12px;margin-bottom:17px}
.amen-list svg{flex:none;margin-top:2px}
.chevron{left:572px;top:1414px;width:56px;height:56px;border-radius:50%;background:var(--white);display:flex;align-items:center;justify-content:center}

/* membership */
.mem-title{left:112px;top:1533px;font-size:40px}
.mem-text{left:112px;width:455px;top:1611px;font-size:14px;line-height:26px}
.mem-text p{margin-bottom:26px}
.price-card{left:600px;top:1543px;width:438px;height:492px;border-radius:30px;background:var(--white);box-shadow:0 6px 24px rgba(0,0,0,.12);overflow:hidden;border-bottom:5px solid var(--blue)}
.price-top{height:199px;background:var(--blue);text-align:center;color:var(--white);padding-top:56px}
.price-top .small{font-family:'Montserrat',sans-serif;font-weight:700;font-size:13px}
.price-top .big{font-family:'Montserrat',sans-serif;font-weight:700;font-size:40px;margin-top:6px}
.price-top .bar{width:56px;height:3px;background:var(--white);margin:16px auto 0}
.price-body{padding:26px 34px 0;text-align:center;font-size:14px;line-height:26px}
.price-body p{margin-bottom:26px}

/* photos */
.photos-title{left:0;width:1200px;top:2118px;text-align:center;font-size:40px}
.gallery{left:112px;top:2218px;width:976px;height:375px;display:grid;grid-template-columns:repeat(4,1fr);grid-template-rows:repeat(2,1fr)}
.gallery div{width:100%;height:100%}

/* philosophy */
.phil-band{left:0;top:2689px;width:1200px;height:448px;background:var(--blue)}
.phil-title{left:0;width:1200px;top:2752px;text-align:center;font-size:40px;color:var(--white)}
.phil-card{top:2845px;width:475px;height:360px;background:var(--card-dark);box-shadow:0 8px 20px rgba(0,0,0,.25)}
.phil-img{width:100%;height:239px}
.phil-card h3{font-family:'Lato',sans-serif;font-weight:700;font-size:17px;color:var(--white);margin:15px 33px 6px}
.phil-card p{font-size:12.5px;line-height:20.5px;color:var(--white);margin:0 33px}
.arrow{top:3007px;width:50px;height:50px;border-radius:50%;background:var(--white);display:flex;align-items:center;justify-content:center;box-shadow:0 2px 6px rgba(0,0,0,.15)}

/* contact */
.pin{width:38px;height:38px;border-radius:50%;background:var(--blue);display:flex;align-items:center;justify-content:center}
.c-label{left:206px;font-size:13.5px}
.c-lines{left:238px;font-size:13.5px;line-height:26px}
.social{top:3693px;width:38px;height:38px;border-radius:50%;background:var(--blue)}
.contact-title{left:581px;top:3292px;font-size:37px}
.field{border:1px solid var(--line);border-radius:3px;font-size:13px;color:#8a9096;padding:15px 15px}
.submit{left:952px;top:3669px;width:140px;height:53px;border-radius:27px;background:var(--blue);color:var(--white);font-weight:700;font-size:16px;display:flex;align-items:center;justify-content:center}

/* footer */
.footer{left:0;top:3828px;width:1200px;height:71px;background:var(--blue);color:var(--white);font-size:13px;display:flex;align-items:center;justify-content:center}
</style>
</head>
<body>

<!-- Hero -->
<section class="abs hero" role="img" aria-label="Photo of the coworking space with long wooden tables and pendant lamps"></section>
<div class="abs hero-shade"></div>
<div class="abs brand">DESKHAVEN<br>COWORK</div>
<nav class="abs nav">
  <span class="active">HOME</span><span>ABOUT</span><span>AMENITIES</span><span>MEMBERSHIP</span><span>PICTURES</span><span>THE DESKHAVEN PHILOSOPHY</span><span>CONTACT</span>
</nav>
<h1 class="abs hero-title">DESKHAVEN COWORK</h1>
<p class="abs hero-sub">Free yourself for the burdens of house or school, and work in an environment<br>that MOTIVATES you instead of DISTRACTS you</p>
<div class="abs btn-start">GET STARTED</div>
<div class="abs dots"><i class="on"></i><i></i><i></i><i></i></div>

<!-- About -->
<h2 class="abs heading about-title">ABOUT DESKHAVEN COSPACE</h2>
<p class="abs about-text">DESKHAVEN is Galveston's first (and currently only) shared business co-working space.&nbsp; We share the same upscale, casual work environment, but we work independently on our own (or our team's) projects and goals.&nbsp; For only a flat $195 membership fee per month, you have your very own all-inclusive, fun, personal business office environment.</p>

<!-- Amenities -->
<div class="abs amen-photo" role="img" aria-label="Photo of the lounge with black leather sofa, plant and red lockers"></div>
<div class="abs amen-panel"></div>
<h2 class="abs heading amen-title">AMENITIES</h2>
<div class="rule" style="left:660px;top:1088px;width:100px;background:var(--white)"></div>
<ul class="abs amen-list">
  <li><svg width="13" height="13" viewBox="0 0 13 13"><circle cx="6.5" cy="6.5" r="6.5" fill="#fff"/><path d="M3.6 6.7l2 2 3.8-4" stroke="#35a8e0" stroke-width="1.8" fill="none"/></svg>Open office or a private cubicle for your daily use.</li>
  <li><svg width="13" height="13" viewBox="0 0 13 13"><circle cx="6.5" cy="6.5" r="6.5" fill="#fff"/><path d="M3.6 6.7l2 2 3.8-4" stroke="#35a8e0" stroke-width="1.8" fill="none"/></svg>Free Wifi.</li>
  <li><svg width="13" height="13" viewBox="0 0 13 13"><circle cx="6.5" cy="6.5" r="6.5" fill="#fff"/><path d="M3.6 6.7l2 2 3.8-4" stroke="#35a8e0" stroke-width="1.8" fill="none"/></svg>24 hour access.</li>
  <li><svg width="13" height="13" viewBox="0 0 13 13"><circle cx="6.5" cy="6.5" r="6.5" fill="#fff"/><path d="M3.6 6.7l2 2 3.8-4" stroke="#35a8e0" stroke-width="1.8" fill="none"/></svg>Comfortable open casual spaces or private office cubicles – at your option.</li>
  <li><svg width="13" height="13" viewBox="0 0 13 13"><circle cx="6.5" cy="6.5" r="6.5" fill="#fff"/><path d="M3.6 6.7l2 2 3.8-4" stroke="#35a8e0" stroke-width="1.8" fill="none"/></svg>Communal coffee bar and kitchen, with FREE coffee.</li>
  <li><svg width="13" height="13" viewBox="0 0 13 13"><circle cx="6.5" cy="6.5" r="6.5" fill="#fff"/><path d="M3.6 6.7l2 2 3.8-4" stroke="#35a8e0" stroke-width="1.8" fill="none"/></svg><span>Health and social distance amenities, including hand washing stations, and distanced desks with glass or wall separations, rigorous cleaning and sanitizing schedules.</span></li>
  <li><svg width="13" height="13" viewBox="0 0 13 13"><circle cx="6.5" cy="6.5" r="6.5" fill="#fff"/><path d="M3.6 6.7l2 2 3.8-4" stroke="#35a8e0" stroke-width="1.8" fill="none"/></svg>Use of copier/printer (at per-copy cost).</li>
</ul>
<div class="abs chevron"><svg width="20" height="16" viewBox="0 0 20 16"><path d="M3 2l7 6 7-6M3 8l7 6 7-6" stroke="#1b1b1b" stroke-width="1.6" fill="none"/></svg></div>

<!-- Membership -->
<h2 class="abs heading mem-title">MEMBERSHIP</h2>
<div class="rule" style="left:112px;top:1593px;width:100px"></div>
<div class="abs mem-text">
  <p>Lorem ipsum dolor sit amet, consectetur adipiscing elit, sed do eiusmod tempor incididunt ut labore et dolore magna aliqua. Ut enim ad minim veniam, quis nostrud exercitation ullamco laboris nisi ut aliquip ex ea commodo consequat. Duis aute irure dolor in reprehenderit in voluptate velit esse cillum dolore eu fugiat nulla pariatur. Excepteur sint occaecat cupidatat non proident, sunt in culpa qui officia deserunt mollit anim id est laborum.</p>
  <p>Lorem ipsum dolor sit amet, consectetur adipiscing elit, sed do eiusmod tempor incididunt ut labore et dolore magna aliqua. Ut enim ad minim veniam, quis nostrud exercitation ullamco laboris nisi ut aliquip ex ea commodo consequat. Duis aute irure dolor in reprehenderit in voluptate velit esse cillum dolore eu fugiat nulla pariatur. Excepteur sint occaecat cupidatat non proident, sunt in culpa qui officia deserunt mollit anim id est laborum.</p>
</div>
<div class="abs price-card">
  <div class="price-top">
    <div class="small">FOR ONLY</div>
    <div class="big">$195 A MONTH</div>
    <div class="bar"></div>
  </div>
  <div class="price-body">
    <p>WiFi, coffee, use of the conference room, office use, use of the kitchen and all the other features listed under "AMENITIES" above, are INCLUDED at no additional cost.</p>
    <p>Get a FREE day, to try us out by emailing us at the link here (link).</p>
    <p>(Need to make an email form that requests name, address, phone, emailand description of business).</p>
  </div>
</div>

<!-- Photos -->
<h2 class="abs heading photos-title">PHOTOS</h2>
<div class="rule" style="left:550px;top:2178px;width:100px"></div>
<div class="abs gallery">
  <div role="img" aria-label="Photo of open lounge and desks" style="background:linear-gradient(135deg,#c9c3b2,#8a7a5c 50%,#3a3634)"></div>
  <div role="img" aria-label="Photo of private cubicles with yellow chair" style="background:linear-gradient(135deg,#d6d8da,#8c8f92 50%,#4a4a3e)"></div>
  <div role="img" aria-label="Photo of wooden work tables under lamps" style="background:linear-gradient(135deg,#5a5148,#b58a3c 55%,#d2a048)"></div>
  <div role="img" aria-label="Photo of hallway with plants" style="background:linear-gradient(135deg,#d8d6d0,#9a8f80 50%,#6c6a5a)"></div>
  <div role="img" aria-label="Photo of kitchen counter" style="background:linear-gradient(135deg,#d9d0a8,#b99a5c 55%,#5a2a30)"></div>
  <div role="img" aria-label="Photo of lockers and sofa" style="background:linear-gradient(135deg,#e0ddd6,#7a3038 50%,#2a2a2a)"></div>
  <div role="img" aria-label="Photo of kitchen with fruit bowl" style="background:linear-gradient(135deg,#5a4a48,#8a7a6a 50%,#d8a070)"></div>
  <div role="img" aria-label="Photo of coffee bar with stools" style="background:linear-gradient(135deg,#c9c6be,#7a4a4a 55%,#4a1e28)"></div>
</div>

<!-- Philosophy -->
<div class="abs phil-band"></div>
<h2 class="abs heading phil-title">THE DESKHAVEN PHILOSOPHY</h2>
<div class="rule" style="left:550px;top:2814px;width:100px;background:var(--white)"></div>
<div class="abs phil-card" style="left:112px">
  <div class="phil-img" role="img" aria-label="Photo of the open lounge and work tables" style="background:linear-gradient(135deg,#4a4442,#cfc8b6 45%,#b08a44 80%,#8a6a3a)"></div>
  <h3>DESKHAVEN THE COMPETITION</h3>
  <p>Free yourself for the burdens of house or school, and work in an environment that MOTIVATES you instead of DISTRACTS you. Meet like-minded people that can help</p>
</div>
<div class="abs phil-card" style="left:613px">
  <div class="phil-img" role="img" aria-label="Photo of private office with copier" style="background:linear-gradient(135deg,#d2cfc8,#9a9690 45%,#6a6662 80%,#4a4644)"></div>
  <h3>DESKHAVEN THE COMPETITION</h3>
  <p>Because of the flexibility, prestigious location, opportunities to meet and network with active professionals, and the available tech and amenities, you have all the tools you need</p>
</div>
<div class="abs arrow" style="left:29px"><svg width="12" height="14" viewBox="0 0 12 14"><path d="M8 2L3 7l5 5" stroke="#1b1b1b" stroke-width="1.6" fill="none"/></svg></div>
<div class="abs arrow" style="left:1119px"><svg width="12" height="14" viewBox="0 0 12 14"><path d="M4 2l5 5-5 5" stroke="#1b1b1b" stroke-width="1.6" fill="none"/></svg></div>

<!-- Contact info -->
<div class="abs pin" style="left:152px;top:3308px"><svg width="12" height="16" viewBox="0 0 12 16"><path d="M6 0a6 6 0 0 0-6 6c0 4.5 6 10 6 10s6-5.5 6-10a6 6 0 0 0-6-6z" fill="#fff"/><circle cx="6" cy="6" r="2.2" fill="#35a8e0"/></svg></div>
<div class="abs c-label" style="top:3319px">Physical location:</div>
<div class="abs c-lines" style="top:3341px">Deskhaven Cospace<br>418 Seawall Row, Suite 101<br>Galveston, TX 77550</div>

<div class="abs pin" style="left:152px;top:3411px"><svg width="12" height="16" viewBox="0 0 12 16"><path d="M6 0a6 6 0 0 0-6 6c0 4.5 6 10 6 10s6-5.5 6-10a6 6 0 0 0-6-6z" fill="#fff"/><circle cx="6" cy="6" r="2.2" fill="#35a8e0"/></svg></div>
<div class="abs c-label" style="top:3422px">Owner:</div>
<div class="abs c-lines" style="top:3444px">Harborline Holdings<br>office@harborlineholdings.com<br>713-555-0142</div>

<div class="abs pin" style="left:152px;top:3540px"><svg width="12" height="16" viewBox="0 0 12 16"><path d="M6 0a6 6 0 0 0-6 6c0 4.5 6 10 6 10s6-5.5 6-10a6 6 0 0 0-6-6z" fill="#fff"/><circle cx="6" cy="6" r="2.2" fill="#35a8e0"/></svg></div>
<div class="abs c-label" style="top:3551px">Mailing address for management:</div>
<div class="abs c-lines" style="top:3598px">Harborline Holdings<br>150 Bayou Street, Suite 200<br>Houston, TX 77002</div>

<div class="abs social" style="left:152px" aria-label="Social profile"></div>
<div class="abs social" style="left:222px" aria-label="Social profile"></div>
<div class="abs social" style="left:291px" aria-label="Social profile"></div>
<div class="abs social" style="left:359px" aria-label="Social profile"></div>

<!-- Contact form -->
<h2 class="abs heading contact-title">GET IN TOUCH WITH ME</h2>
<div class="abs field" style="left:581px;top:3364px;width:248px;height:48px">Name:</div>
<div class="abs field" style="left:838px;top:3364px;width:248px;height:48px">Email:</div>
<div class="abs field" style="left:581px;top:3428px;width:248px;height:49px">Phone:</div>
<div class="abs field" style="left:838px;top:3428px;width:248px;height:49px">Subject:</div>
<div class="abs field" style="left:581px;top:3491px;width:505px;height:168px">Message:</div>
<div class="abs submit">SUBMIT</div>

<!-- Footer -->
<footer class="abs footer">© Copyrights 2020 Company name | All Rights Reserved</footer>

</body>
</html>
```